Rack Card Design Project

We are a locally family owned public golf course. We would like to have a rack card designed that can be used for multiple applications. The colors in our logo are grey, blue, and white. Please use those in the card design. The company logo, contact information, address, and summer pricing should be included. I've included some pictures that may or may not be used. I'm also open to suggestions....use one photo, multiple photos, a stock photo or image representing golf etc.

```html
<!DOCTYPE html>
<html lang="en">
<head>
<meta charset="utf-8">
<title>Harbor Pines Golf Club – Summer Rates Rack Card</title>
<link href="https://fonts.googleapis.com/css2?family=Crimson+Pro:wght@500;600;700&display=swap" rel="stylesheet">
<style>
  :root {
    --navy: #14365f;
    --grey: #a9a9ab;
    --grey-light: #c9c9cb;
    --sky: #cbe8f8;
    --white: #ffffff;
    --page: #8e8e8e;
    --ink: #1b1b1b;
  }
  * { box-sizing: border-box; margin: 0; padding: 0; }
  html, body { width: 672px; height: 1200px; overflow: hidden; }
  body {
    background: var(--page);
    font-family: "Crimson Pro", Georgia, serif;
    position: relative;
  }
  .rack-card {
    position: absolute; left: 76px; top: 20px;
    width: 519px; height: 1160px;
    background: var(--white);
    overflow: hidden;
    box-shadow: 0 6px 18px rgba(0,0,0,.35);
  }
  .hero-photo {
    position: absolute; left: 0; top: 85px; width: 519px; height: 300px;
    background: radial-gradient(ellipse at 30% 20%, #f3d9a0 0%, #c9b377 25%, transparent 55%),
                linear-gradient(180deg, #9aa27a 0%, #7fa24e 55%, #5f8c34 100%);
    clip-path: ellipse(75% 100% at 50% 0%);
  }
  .brand {
    position: absolute; left: 24px; top: 36px;
    display: flex; align-items: center; gap: 12px;
    z-index: 2;
  }
  .brand-dot { width: 30px; height: 30px; border-radius: 50%; background: var(--navy); }
  .brand-name { font-size: 30px; font-weight: 600; color: var(--navy); }
  .course-photo {
    position: absolute; border-radius: 50%;
    border: 5px solid var(--navy);
    box-shadow: 0 3px 8px rgba(0,0,0,.3);
  }
  .course-photo.one { left: 19px; top: 347px; width: 190px; height: 190px;
    background: linear-gradient(180deg, #dbe4ea 0%, #9cb0a8 45%, #4f7236 70%, #3d5f2a 100%); }
  .course-photo.two { left: 214px; top: 421px; width: 160px; height: 160px;
    background: linear-gradient(180deg, #b9c0c8 0%, #d8b488 40%, #5d6f3c 70%, #466130 100%); }
  .course-photo.three { left: 374px; top: 369px; width: 132px; height: 132px;
    background: linear-gradient(180deg, #3f7cc4 0%, #7ba6d6 45%, #4f7a3a 70%, #8a7a5a 100%); }
  .rates-title {
    position: absolute; top: 600px; width: 100%; text-align: center;
    font-size: 46px; font-weight: 700; color: var(--navy);
  }
  .pill {
    position: absolute; left: 94px; width: 333px;
    background: var(--navy); color: var(--white);
    border-radius: 22px; text-align: center;
  }
  .pill.season { top: 657px; height: 38px; font-size: 26px; line-height: 38px; font-weight: 500; }
  .pill.lunch { top: 936px; height: 41px; font-size: 18px; line-height: 41px; font-weight: 600; }
  .rates-table {
    position: absolute; left: 63px; top: 710px; width: 383px;
    border-collapse: separate; border-spacing: 0 3px;
    box-shadow: 6px 8px 10px rgba(0,0,0,.3);
    font-size: 18px; font-weight: 600;
  }
  .rates-table td { height: 32px; padding: 0 14px; }
  .rates-table td.price { width: 78px; text-align: left; border-left: 3px solid var(--white); color: var(--ink); }
  .rates-table tr.category td { background: var(--grey); color: var(--navy); }
  .rates-table tr.category td.price { color: var(--white); }
  .rates-table tr.slot td { background: var(--sky); color: var(--ink); }
  .footer-curve { position: absolute; left: 0; top: 985px; width: 519px; height: 175px; }
  .contact {
    position: absolute; top: 1016px; width: 100%; text-align: center;
    color: var(--ink); font-weight: 600;
  }
  .contact .club { font-size: 16px; margin-bottom: 8px; }
  .contact .line { display: flex; justify-content: center; align-items: center; gap: 8px; }
  .contact .address { font-size: 16px; margin-bottom: 6px; }
  .contact .phone { font-size: 21px; margin-bottom: 4px; }
  .contact .web { font-size: 21px; }
  .icon { width: 18px; height: 18px; }
</style>
</head>
<body>
  <main class="rack-card">
    <div class="hero-photo" role="img" aria-label="Golf ball beside an iron club on a green at sunrise"></div>
    <div class="brand">
      <span class="brand-dot"></span>
      <span class="brand-name">Harbor Pines Golf Club</span>
    </div>
    <div class="course-photo one" role="img" aria-label="Fairway lined with pine trees"></div>
    <div class="course-photo two" role="img" aria-label="Course trees at sunset"></div>
    <div class="course-photo three" role="img" aria-label="Green under a blue sky"></div>

    <h1 class="rates-title">Summer Rates</h1>
    <div class="pill season">May 1 – September 30</div>

    <table class="rates-table">
      <tr class="category"><td>18 Holes With Cart</td><td class="price"></td></tr>
      <tr class="slot"><td>7AM – 11AM</td><td class="price">$24</td></tr>
      <tr class="slot"><td>11AM – 3PM</td><td class="price">$19</td></tr>
      <tr class="slot"><td>3PM – Close</td><td class="price">$15</td></tr>
      <tr class="category"><td>9 Holes With Cart</td><td class="price">$15</td></tr>
      <tr class="category"><td>Walking</td><td class="price">$12</td></tr>
    </table>

    <div class="pill lunch">Lunch Available Daily : 10AM – 3PM</div>

    <svg class="footer-curve" viewBox="0 0 519 175" preserveAspectRatio="none" aria-hidden="true">
      <path d="M0 40 Q260 -20 519 40 L519 175 L0 175 Z" fill="var(--grey-light)"/>
      <path d="M0 40 Q260 -20 519 40" fill="none" stroke="var(--navy)" stroke-width="6"/>
    </svg>

    <div class="contact">
      <p class="club">Harbor Pines Golf Club</p>
      <p class="line address">
        <svg class="icon" viewBox="0 0 20 20"><circle cx="10" cy="10" r="10" fill="var(--ink)"/><path d="M10 4a4 4 0 0 0-4 4c0 3 4 8 4 8s4-5 4-8a4 4 0 0 0-4-4z" fill="#fff"/><circle cx="10" cy="8" r="1.5" fill="var(--ink)"/></svg>
        2450 SW Cedar Bend Rd Palm Cove, FL 34000
      </p>
      <p class="line phone">
        <svg class="icon" viewBox="0 0 20 20"><circle cx="10" cy="10" r="10" fill="var(--ink)"/><path d="M7 5l2 3-1 1a7 7 0 0 0 3 3l1-1 3 2-1 2c-4 0-8-4-8-8z" fill="#fff"/></svg>
        555-214-0387
      </p>
      <p class="line web">
        <svg class="icon" viewBox="0 0 20 20"><circle cx="10" cy="10" r="10" fill="var(--ink)"/><circle cx="10" cy="10" r="6" fill="none" stroke="#fff" stroke-width="1.3"/><path d="M4 10h12M10 4c-3 3-3 9 0 12M10 4c3 3 3 9 0 12" fill="none" stroke="#fff" stroke-width="1.1"/></svg>
        www.harborpinesgc.com
      </p>
    </div>
  </main>
</body>
</html>
```